Oil and Gas Exploration and Production company needs a business card design

We need a business card design using our logo and colors in the logo. We want a mainstream design.

```html
<!DOCTYPE html>
<html lang="en">
<head>
<meta charset="utf-8">
<title>Vesta Oil &amp; Gas — Business Card</title>
<link rel="stylesheet" href="https://fonts.googleapis.com/css2?family=Arvo:wght@400;700&family=Courier+Prime:wght@400;700&display=swap">
<style>
  :root {
    --backdrop: #e7e2da;
    --paper: #f7f7f5;
    --ink: #1d1d1d;
    --gold: #c49a2c;
    --gold-deep: #a9831f;
    --muted: #3a3a3a;
  }
  * { box-sizing: border-box; margin: 0; padding: 0; }
  html, body { width: 1200px; height: 911px; overflow: hidden; }
  body {
    background: var(--backdrop);
    font-family: "Courier Prime", "Courier New", monospace;
    color: var(--ink);
  }
  .canvas {
    position: relative;
    width: 1200px;
    height: 911px;
    display: flex;
    justify-content: center;
    align-items: center;
    gap: 110px;
  }
  .card {
    width: 330px;
    height: 578px;
    border-radius: 18px;
    box-shadow: 0 6px 18px rgba(0,0,0,0.18);
    position: relative;
  }
  .card-front {
    background: var(--paper);
    display: flex;
    flex-direction: column;
    align-items: center;
    padding-top: 86px;
  }
  .wordmark {
    display: flex;
    align-items: center;
    gap: 10px;
    font-family: "Arvo", Georgia, serif;
    font-weight: 700;
    color: var(--ink);
  }
  .wordmark-dot {
    width: 20px; height: 20px;
    border-radius: 50%;
    background: var(--gold);
    flex: none;
  }
  .card-front .wordmark-name { font-size: 38px; letter-spacing: -0.5px; line-height: 1; }
  .person { margin-top: 64px; text-align: center; }
  .person-name {
    font-family: "Arvo", Georgia, serif;
    font-weight: 700;
    font-size: 17px;
    letter-spacing: 1.5px;
  }
  .person-role {
    font-family: "Arvo", Georgia, serif;
    font-size: 13px;
    letter-spacing: 1px;
    color: var(--gold);
    margin-top: 3px;
  }
  .divider {
    width: 70px; height: 1px;
    background: var(--ink);
    position: relative;
    margin: 20px auto;
  }
  .divider::after {
    content: "";
    position: absolute;
    left: 25px; top: -1.5px;
    width: 20px; height: 4px;
    border-radius: 2px;
    background: var(--gold);
  }
  .address { text-align: center; font-size: 13px; line-height: 1.35; color: var(--muted); }
  .contact { list-style: none; font-size: 13px; line-height: 1.5; color: var(--muted); align-self: center; }
  .contact li { display: flex; align-items: center; gap: 7px; }
  .contact svg { width: 11px; height: 11px; fill: var(--ink); flex: none; }
  .card-back {
    background: var(--gold);
    display: flex;
    flex-direction: column;
    align-items: center;
    justify-content: center;
  }
  .back-mark {
    display: flex;
    flex-direction: column;
    align-items: center;
    gap: 18px;
    margin-top: -40px;
  }
  .back-mark .wordmark-dot { width: 110px; height: 110px; background: var(--ink); }
  .back-mark .wordmark-name {
    font-family: "Arvo", Georgia, serif;
    font-weight: 700;
    font-size: 28px;
    color: var(--ink);
  }
  .back-web {
    position: absolute;
    bottom: 40px;
    left: 0; right: 0;
    text-align: center;
    font-family: "Arvo", Georgia, serif;
    font-size: 12px;
    letter-spacing: 4px;
    color: #fff;
  }
</style>
</head>
<body>
<main class="canvas">
  <section class="card card-front" aria-label="Card front">
    <div class="wordmark">
      <span class="wordmark-dot"></span>
      <span class="wordmark-name">Vesta Oil &amp; Gas</span>
    </div>
    <div class="person">
      <p class="person-name">MARA ELLISON</p>
      <p class="person-role">CEO/FOUNDER</p>
    </div>
    <div class="divider"></div>
    <p class="address">214 Larch Ridge Road<br>Juneau, Alaska 99801</p>
    <div class="divider"></div>
    <ul class="contact">
      <li><svg viewBox="0 0 12 12"><path d="M2.5 1 4.5 1 5.2 3.6 3.9 4.5Q5 7 7.5 8.1L8.4 6.8 11 7.5 11 9.5Q10.5 11 9 11 1 10 1 2.5 1 1.5 2.5 1Z"/></svg>907 555 0142</li>
      <li><svg viewBox="0 0 12 12"><path d="M3 1h6v3H3zM1 4.5h10v5H9V11H3V9.5H1zM4 7.5v2.5h4V7.5z"/></svg>907 555 0187</li>
      <li><svg viewBox="0 0 12 12"><path d="M3 2h6v3H3zM1 5.5h10V10H1z"/></svg>907 555 0163</li>
      <li><svg viewBox="0 0 12 12"><path d="M1 2.5h10v7H1zM1.8 3.2 6 6.5 10.2 3.2" stroke="#f7f7f5" stroke-width="0.9"/></svg>info@vestaoilgas.com</li>
      <li><svg viewBox="0 0 12 12"><circle cx="6" cy="6" r="5"/></svg>www.vestaoilgas.com</li>
    </ul>
  </section>

  <section class="card card-back" aria-label="Card back">
    <div class="back-mark wordmark">
      <span class="wordmark-dot"></span>
      <span class="wordmark-name">Vesta Oil &amp; Gas</span>
    </div>
    <p class="back-web">www.vestaoilgas.com</p>
  </section>
</main>
</body>
</html>
```